We need a logo design that explain all the products we possess.
The main goal is to represent graphically all the logos, pointing to one single logo - Vellamor.
The descriptions are in french.
I have uploaded a file with 4 logos to use:
Vellamor (the logo that all the rest should be pointing to)
RTN
Ombrevik
TroupéLune
All logo must be used in the vector graphic format, the description file is in each folder, it's the description that should be next to the logo.

The main goal of this is to create a banner 10' x 11' (estimated)

Target Market(s)

Cities

Requirements
Must have
• All the logos in the zip file in vector graphic.
Nice to have
• A background
Should not have
• Do not use KOL logo, it's a mix with RTN, and Kol Blue/dark blue with inscription "RTN", Charging fees for a part of the picture is not ok!

```html
<!DOCTYPE html>
<html lang="fr">
<head>
<meta charset="utf-8">
<title>Portail Vellamors 2.0 – bannière</title>
<link href="https://fonts.googleapis.com/css2?family=Montserrat:wght@600;700;800&display=swap" rel="stylesheet">
<style>
  :root {
    --page: #ececec;
    --ink: #111111;
    --brand-blue: #1a6fb5;
    --ring-grey: #e3e3e5;
    --white: #ffffff;
    --green: #8dc63f;
    --teal: #62aab0;
    --sky-blue: #1e9be0;
    --sky-top: #2f6fbf;
    --sky-mid: #8fb4dc;
    --sky-low: #e9ecef;
    --city-top: #b9c7cf;
    --city-low: #5b5a52;
  }
  html, body {
    margin: 0;
    width: 1200px;
    height: 1200px;
    overflow: hidden;
    background: var(--page);
  }
  .banner {
    position: absolute;
    left: 104px;
    top: 54px;
    width: 993px;
    height: 1091px;
  }
  .banner svg { display: block; width: 100%; height: 100%; }
  .label {
    font-family: "Montserrat", sans-serif;
    font-weight: 700;
    font-size: 48px;
    fill: var(--ink);
    text-anchor: middle;
    letter-spacing: 1px;
  }
  .brand-name {
    font-family: "Montserrat", sans-serif;
    font-weight: 800;
    text-anchor: middle;
    fill: var(--brand-blue);
  }
  .brand-name--lune { fill: var(--sky-blue); }
</style>
</head>
<body>
<div class="banner">
  <svg viewBox="168 87 1598 1756" xmlns="http://www.w3.org/2000/svg">
    <defs>
      <linearGradient id="skyGrad" x1="0" y1="0" x2="0" y2="1">
        <stop offset="0" stop-color="#2f6fbf"/>
        <stop offset="0.45" stop-color="#8fb4dc"/>
        <stop offset="1" stop-color="#e9ecef"/>
      </linearGradient>
      <linearGradient id="cityGrad" x1="0" y1="0" x2="0" y2="1">
        <stop offset="0" stop-color="#e9ecef" stop-opacity="0"/>
        <stop offset="0.35" stop-color="#b9c7cf"/>
        <stop offset="1" stop-color="#5b5a52"/>
      </linearGradient>
    </defs>

    <rect class="sky" x="168" y="87" width="1598" height="1756" fill="url(#skyGrad)" role="img" aria-label="Photo de ciel bleu nuageux"/>
    <rect class="skyline" x="168" y="1370" width="1598" height="445" fill="url(#cityGrad)" role="img" aria-label="Photo d'une ligne d'horizon urbaine avec gratte-ciel"/>
    <rect class="footer-band" x="168" y="1815" width="1598" height="28" fill="var(--green)"/>

    <g class="hub">
      <path d="M553 575 A415 415 0 0 1 1385 575" fill="none" stroke="var(--ink)" stroke-width="5"/>
      <path d="M553 575 A415 415 0 0 0 1385 575" fill="none" stroke="var(--ink)" stroke-width="5" stroke-dasharray="22 12"/>
      <circle cx="968" cy="572" r="412" fill="var(--white)"/>
      <circle cx="968" cy="572" r="372" fill="var(--ring-grey)"/>
      <circle cx="970" cy="570" r="315" fill="var(--white)"/>
      <circle cx="555" cy="575" r="18" fill="var(--white)" stroke="var(--ink)" stroke-width="7"/>
      <circle cx="1385" cy="575" r="18" fill="var(--white)" stroke="var(--ink)" stroke-width="7"/>
      <text class="brand-name" x="966" y="640" font-size="74">VELLAMORS</text>
      <text class="label" x="968" y="718">PORTAIL</text>
      <text class="label" x="968" y="775">VELLAMORS 2.0</text>
    </g>

    <path d="M680 870 L830 960" stroke="var(--green)" stroke-width="6" stroke-dasharray="20 10"/>
    <path d="M1250 875 L1095 965" stroke="var(--sky-blue)" stroke-width="6" stroke-dasharray="20 10"/>

    <g class="product product--rtn">
      <polygon points="686,730 605,722 680,803" fill="var(--green)"/>
      <line x1="580" y1="860" x2="650" y2="765" stroke="var(--green)" stroke-width="26"/>
      <circle cx="517" cy="888" r="153" fill="var(--white)" stroke="var(--green)" stroke-width="22"/>
      <text class="brand-name" x="517" y="910" font-size="64">RTN</text>
      <text class="label" x="508" y="1112">CONSEIL</text>
      <text class="label" x="508" y="1170">SANS PAPIER</text>
    </g>

    <g class="product product--ombrevik">
      <polygon points="905,890 965,843 1025,890" fill="var(--teal)"/>
      <rect x="935" y="885" width="60" height="40" fill="var(--teal)"/>
      <circle cx="965" cy="1068" r="153" fill="var(--white)" stroke="var(--teal)" stroke-width="22"/>
      <text class="brand-name" x="965" y="1082" font-size="36">OMBREVIK</text>
      <text class="label" x="968" y="1286">PERMIS | CARTE</text>
      <text class="label" x="968" y="1345">INVENTAIRE | TAXES</text>
    </g>

    <g class="product product--troupelune">
      <polygon points="1248,735 1330,720 1256,808" fill="var(--sky-blue)"/>
      <line x1="1340" y1="850" x2="1275" y2="770" stroke="var(--sky-blue)" stroke-width="26"/>
      <circle cx="1412" cy="888" r="153" fill="var(--white)" stroke="var(--sky-blue)" stroke-width="22"/>
      <text class="brand-name brand-name--lune" x="1412" y="900" font-size="34">TroupéLune</text>
      <text class="label" x="1425" y="1112">LICENCES</text>
      <text class="label" x="1425" y="1170">POUR ANIMAUX</text>
    </g>
  </svg>
</div>
</body>
</html>
```